Awesome Beer Labels for food pairing

We are going to launch a range of craft beers specially brewed for food pairing, and we are in need of a logo and bottle labels to represent this. Every label individually has to show which beer type it is and the food groups it matches with. At the same time the whole range has to have the same appearance as we are promoting it as a whole package. As we are targeting middle-high to high class hospitality businesses we are looking for a luxurious, exclusive feel to the labels. We also need room for a clear title of the beer and a small food pairing description.

Industry/Entity Type

Craft Brewery

Font styles to use
Sans Serif
Decorative
Script

Colors

Designer to choose colors to be used in the design.

Requirements
Must have
• -Different beer labels where the style and name of the beer comes first, and the beer type second
• - A logo for the whole group which also has to be printed on glasses, so nothing to detailed.
• - Clear, recognizable pictures, drawings or symbols for the different food groups.
• - Room for the name of the beer, the beer type and a small description.
Nice to have
• An exclusive, luxurious look and feel that would not stand out in an high class restaurant.
• Something that combines the whole range of beers (something like a overlaying or connecting picture that combines alle the labels?)
Should not have
• To much different styles, the beers have to match

```html
<!DOCTYPE html>
<html lang="en">
<head>
<meta charset="utf-8">
<title>Crestwell Brewery – Craft Beer Label</title>
<link rel="stylesheet" href="https://fonts.googleapis.com/css2?family=Courgette&family=Playfair+Display:wght@400&family=Oswald:wght@300;400&display=swap">
<style>
  :root {
    --backdrop: #e4e6e7;
    --label-black: #020202;
    --gold: #e9c96a;
    --gold-soft: #f3e3a2;
    --gold-deep: #b88a2a;
    --ray: rgba(214, 178, 92, 0.22);
    --cheese: #f0c03a;
    --pizza: #d9893a;
  }
  * { margin: 0; padding: 0; box-sizing: border-box; }
  html, body { width: 1200px; height: 800px; overflow: hidden; }
  body {
    background: var(--backdrop);
    position: relative;
  }
  .beer-label {
    position: absolute;
    left: 327px;
    top: 30px;
    width: 545px;
    height: 740px;
    background: var(--label-black);
    box-shadow: 6px 8px 10px rgba(0, 0, 0, 0.25);
    overflow: hidden;
    text-align: center;
    color: var(--gold);
  }
  .sunburst {
    position: absolute;
    inset: 0;
    background: radial-gradient(ellipse at 50% 62%, var(--ray) 0%, rgba(214,178,92,0.12) 40%, rgba(0,0,0,0) 75%);
  }
  .brand-mark {
    position: absolute;
    top: 80px;
    left: 0;
    right: 0;
    display: flex;
    align-items: center;
    justify-content: center;
    gap: 10px;
    font-family: "Playfair Display", serif;
    font-size: 26px;
    color: var(--gold);
  }
  .brand-dot {
    width: 14px;
    height: 14px;
    border-radius: 50%;
    background: var(--gold);
  }
  .flourish {
    position: absolute;
    top: 196px;
    left: 182px;
    width: 180px;
    height: 30px;
    background: linear-gradient(90deg, rgba(233,201,106,0) 0%, var(--gold-deep) 30%, var(--gold) 50%, var(--gold-deep) 70%, rgba(233,201,106,0) 100%);
    opacity: 0.7;
    border-radius: 15px;
  }
  .style-script {
    position: absolute;
    top: 222px;
    left: 0;
    right: 0;
    font-family: "Courgette", cursive;
    font-size: 70px;
    line-height: 1;
    color: var(--gold-soft);
  }
  .beer-name {
    position: absolute;
    top: 320px;
    left: 0;
    right: 0;
    font-family: "Playfair Display", serif;
    font-size: 112px;
    line-height: 1;
    letter-spacing: 2px;
    color: var(--gold-soft);
    text-shadow: 0 0 8px rgba(246, 214, 110, 0.85), 0 0 18px rgba(246, 200, 80, 0.55);
  }
  .beer-type {
    position: absolute;
    top: 446px;
    left: 0;
    right: 0;
    font-family: "Courgette", cursive;
    font-size: 38px;
    line-height: 1;
    color: var(--gold-soft);
  }
  .pairing-note {
    position: absolute;
    top: 514px;
    left: 80px;
    right: 80px;
    font-family: "Oswald", sans-serif;
    font-weight: 300;
    font-size: 13px;
    line-height: 1.45;
    color: var(--gold-soft);
  }
  .food-pairing {
    position: absolute;
    top: 566px;
    left: 213px;
    width: 118px;
    height: 76px;
    display: flex;
    gap: 6px;
  }
  .food-cheese {
    flex: 1;
    background: var(--cheese);
    border-radius: 6px;
  }
  .food-pizza {
    flex: 1;
    background: linear-gradient(160deg, var(--pizza), var(--cheese));
    border-radius: 6px;
  }
  .net-volume {
    position: absolute;
    top: 686px;
    left: 0;
    right: 0;
    font-family: "Oswald", sans-serif;
    font-weight: 400;
    font-size: 22px;
    color: var(--gold-soft);
  }
</style>
</head>
<body>
  <main class="beer-label">
    <div class="sunburst" role="img" aria-label="Faint gold sunburst rays radiating across the label"></div>

    <div class="brand-mark">
      <span class="brand-dot"></span>
      <span class="brand-name">Crestwell Brewery</span>
    </div>

    <div class="flourish" role="img" aria-label="Gold scroll ornament beneath the brand name"></div>

    <p class="style-script">Craft</p>
    <h1 class="beer-name">BEER</h1>
    <p class="beer-type">beer type</p>

    <p class="pairing-note">Lorem ipsum dolor sit amet, consectetur adipiscing elit, sed do eiusmod tempor incididunt ut labore et dolore magna .</p>

    <div class="food-pairing">
      <div class="food-cheese" role="img" aria-label="Illustration of a wedge of cheese"></div>
      <div class="food-pizza" role="img" aria-label="Illustration of a slice of pepperoni pizza"></div>
    </div>

    <p class="net-volume">Nt.Wt. 160 ml</p>
  </main>
</body>
</html>
```